TalkHarbor - Language Coaching Services

Sleek, innovative, trendy design for Language Coaching business.

TalkHarbor is a new UK based company that provides Language Coaching services. We offer highly personalized on-line and face to face language courses. We also impart learning techniques workshops based on the latest neuroscience research for second-language acquisition.

Target Market(s)

See attached info

Industry/Entity Type

Consulting

Contact Information for Business Card

TalkHarbor
DaniaKV@talkharbor.co.uk
TalkHarbor.co.uk
London, UK

Font styles to use
Sans Serif

```html
<!DOCTYPE html>
<html lang="en">
<head>
<meta charset="utf-8">
<title>TalkHarbor – Business Card</title>
<link href="https://fonts.googleapis.com/css2?family=Open+Sans:wght@400;600;700&display=swap" rel="stylesheet">
<style>
  :root {
    --page-bg: #e8e9eb;
    --blue-light: #2c8bd0;
    --blue-mid: #1468ad;
    --blue-deep: #0b4d86;
    --frost: #8d969c;
    --frost-dark: #6f7a82;
    --ring-navy: #0d3f6e;
    --disc-light: #dcdcda;
    --disc-shade: #c9cac8;
    --brand-navy: #0e3a5a;
    --text-white: #ffffff;
    --text-soft: #e6f1fa;
  }
  * { margin: 0; padding: 0; box-sizing: border-box; }
  html, body {
    width: 1200px;
    height: 1120px;
    overflow: hidden;
    background: var(--page-bg);
    font-family: "Open Sans", Arial, sans-serif;
  }
  .canvas {
    position: relative;
    width: 1200px;
    height: 1120px;
  }
  .business-card {
    position: absolute;
    left: 100px;
    top: 275px;
    width: 1000px;
    height: 571px;
    overflow: hidden;
    background:
      linear-gradient(180deg, rgba(255,255,255,0.06) 0%, rgba(0,0,0,0.10) 100%),
      linear-gradient(90deg,
        var(--blue-light) 0%,
        var(--blue-mid) 30%,
        var(--blue-deep) 52%,
        var(--frost-dark) 72%,
        var(--frost) 100%);
    box-shadow: 0 18px 40px rgba(0,0,0,0.18);
  }
  .brand-ring {
    position: absolute;
    left: 480px;
    top: 26px;
    width: 520px;
    height: 520px;
    border-radius: 50%;
    background: var(--ring-navy);
  }
  .brand-disc {
    position: absolute;
    left: 512px;
    top: 58px;
    width: 456px;
    height: 456px;
    border-radius: 50%;
    background: radial-gradient(circle at 45% 40%, var(--disc-light) 0%, var(--disc-shade) 100%);
    display: flex;
    flex-direction: column;
    align-items: center;
    justify-content: center;
  }
  .brand-mark {
    width: 128px;
    height: 128px;
    border-radius: 50%;
    border: 11px solid var(--brand-navy);
    margin-top: -30px;
    margin-bottom: 12px;
  }
  .brand-name {
    font-weight: 600;
    font-size: 52px;
    letter-spacing: 1px;
    color: var(--brand-navy);
    line-height: 1;
  }
  .holder {
    position: absolute;
    left: 52px;
    top: 70px;
    color: var(--text-white);
  }
  .holder-name {
    font-weight: 700;
    font-size: 31px;
    line-height: 1.1;
    text-transform: uppercase;
  }
  .holder-title {
    font-weight: 400;
    font-size: 23px;
    line-height: 1.3;
    text-transform: uppercase;
    color: var(--text-soft);
  }
  .contact-list {
    position: absolute;
    left: 52px;
    top: 388px;
    list-style: none;
  }
  .contact-item {
    display: flex;
    align-items: center;
    height: 34.5px;
    font-size: 25px;
    color: var(--text-white);
  }
  .contact-icon {
    width: 24px;
    height: 24px;
    margin-right: 15px;
    flex: none;
  }
</style>
</head>
<body>
<main class="canvas">
  <section class="business-card" aria-label="TalkHarbor business card">
    <div class="brand-ring"></div>
    <div class="brand-disc">
      <div class="brand-mark"></div>
      <div class="brand-name">TalkHarbor</div>
    </div>

    <div class="holder">
      <p class="holder-name">Elena Marsh</p>
      <p class="holder-title">President</p>
    </div>

    <ul class="contact-list">
      <li class="contact-item">
        <svg class="contact-icon" viewBox="0 0 24 24" aria-hidden="true">
          <rect x="6" y="1.5" width="12" height="21" rx="2" fill="none" stroke="#fff" stroke-width="2.2"/>
          <rect x="8.5" y="4.5" width="7" height="12" fill="#fff"/>
          <circle cx="12" cy="19.3" r="1.2" fill="#fff"/>
        </svg>
        <span>020 7946 0381</span>
      </li>
      <li class="contact-item">
        <svg class="contact-icon" viewBox="0 0 24 24" aria-hidden="true">
          <rect x="2" y="5" width="20" height="14" rx="1" fill="#fff"/>
          <path d="M2.5 6 L12 13 L21.5 6" fill="none" stroke="#1468ad" stroke-width="1.6"/>
        </svg>
        <span>Info@talkharbor.co.uk</span>
      </li>
      <li class="contact-item">
        <svg class="contact-icon" viewBox="0 0 24 24" aria-hidden="true">
          <circle cx="12" cy="12" r="10" fill="#fff"/>
          <ellipse cx="12" cy="12" rx="4.2" ry="10" fill="none" stroke="#1468ad" stroke-width="1.4"/>
          <line x1="2" y1="12" x2="22" y2="12" stroke="#1468ad" stroke-width="1.4"/>
        </svg>
        <span>TalkHarbor.co.uk</span>
      </li>
    </ul>
  </section>
</main>
</body>
</html>
```